Dog grooming business card
This is a business card for m dog grooming business like it say above.
In the priorities box below I will have the text that I want on the card.

Industry/Entity Type

Business

Colors

Designer to choose colors to be used in the design.

Requirements
Must have
• My logo and the insurance stamp must be on the card.

Text it must have :

Professional grooming services
Email: lunabrisk@mailvale.net
Text or call 1 705 318 6052
TWF certified/member
Pet first aid certified
Next appointment ___________________________________
Nice to have
• Greens to match my logo

```html
<!DOCTYPE html>
<html lang="en">
<head>
<meta charset="utf-8">
<title>Luna Brisk – Grooming Business Card</title>
<link rel="stylesheet" href="https://fonts.googleapis.com/css2?family=Lobster&family=Arimo:wght@400;700&display=swap">
<style>
  :root {
    --bg: #e9e6df;
    --paper: #ffffff;
    --green: #8dc63f;
    --green-dark: #5f8f22;
    --ink: #1d1d1d;
    --rule: #111111;
    --badge: #d9e6f5;
    --badge-edge: #9fb6d3;
  }
  * { box-sizing: border-box; margin: 0; padding: 0; }
  html, body {
    width: 1200px; height: 800px; overflow: hidden;
    background: var(--bg);
    font-family: "Arimo", Arial, sans-serif;
  }
  .canvas {
    width: 1200px; height: 800px;
    display: flex; align-items: center; justify-content: center; gap: 40px;
  }
  .card {
    position: relative;
    width: 550px; height: 314px;
    background: var(--paper);
    box-shadow: 0 4px 14px rgba(0,0,0,.18);
    overflow: hidden;
  }

  /* Front */
  .brand {
    position: absolute; left: 0; right: 0; top: 46px;
    display: flex; align-items: center; justify-content: center; gap: 12px;
  }
  .brand-dot { width: 18px; height: 18px; border-radius: 50%; background: var(--green); }
  .brand-name {
    font-family: "Lobster", cursive;
    font-size: 40px; color: var(--green-dark); line-height: 1;
  }
  .tagline-row {
    position: absolute; left: 0; right: 0; top: 122px;
    display: flex; align-items: center; gap: 14px;
  }
  .tagline-row::before, .tagline-row::after {
    content: ""; flex: 1; height: 1px; background: var(--rule);
  }
  .tagline {
    font-family: "Lobster", cursive;
    font-size: 30px; color: var(--green); white-space: nowrap;
  }
  .credentials {
    position: absolute; left: 0; right: 0; top: 172px;
    text-align: center; font-size: 14px; color: var(--ink); line-height: 1.3;
  }
  .insurance-badge {
    position: absolute; left: 50%; top: 218px; transform: translateX(-50%);
    width: 70px; height: 30px; border-radius: 5px;
    background: var(--badge); border: 1px solid var(--badge-edge);
  }
  .front-rule {
    position: absolute; left: 0; right: 0; bottom: 30px; height: 1px; background: var(--rule);
  }
  .front-band {
    position: absolute; left: 0; right: 0; bottom: 14px; height: 12px; background: var(--green);
  }

  /* Back */
  .appointment {
    position: absolute; left: 120px; right: 60px; top: 110px;
  }
  .appointment-label {
    font-size: 15px; color: var(--green); letter-spacing: .5px; text-align: center;
    margin-bottom: 22px;
  }
  .dotted-line {
    height: 0; border-top: 2px dotted var(--ink); margin-bottom: 14px;
  }
  .contact {
    margin-top: 4px; font-size: 13px; color: var(--ink); white-space: nowrap;
  }
  .contact .accent { color: var(--green); }
</style>
</head>
<body>
<main class="canvas">
  <section class="card card-front">
    <div class="brand">
      <span class="brand-dot"></span>
      <span class="brand-name">Luna Brisk</span>
    </div>
    <div class="tagline-row"><span class="tagline">Professional grooming services</span></div>
    <p class="credentials">TWF certified/member<br>Pet first aid certified</p>
    <div class="insurance-badge" role="img" aria-label="Insurance stamp"></div>
    <div class="front-rule"></div>
    <div class="front-band"></div>
  </section>

  <section class="card card-back">
    <div class="appointment">
      <p class="appointment-label">NEXT APPOINTMENT</p>
      <div class="dotted-line"></div>
      <div class="dotted-line"></div>
      <p class="contact"><span class="accent">Email</span> lunabrisk@mailvale.net / <span class="accent">Text</span> or <span class="accent">Call</span> 1 705 318 6052</p>
    </div>
  </section>
</main>
</body>
</html>
```